Business Card - connecting 2 souls and beggining the journey of self discovery

Logo on the front
with tag line

On the back list of services and contact details

Seminars
workshops
Coaching
podcasts

Darren Whitlow
Health & Wellbeing Life Coach
0491 372 615
darren@brightcoreliving.example
brightcoreliving.example

Industry/Entity Type

Life Coaching

Contact Information for Business Card

I like the use of colour from the logo to be used. I'm not a fan of white.

Requirements
Must have
• My tagline: The journey home starts with you
Nice to have
• Use of colour that is in the mind body soul logo

```html
<!DOCTYPE html>
<html lang="en">
<head>
<meta charset="utf-8">
<title>Bright Core Living – Business Card</title>
<link rel="stylesheet" href="https://fonts.googleapis.com/css2?family=Mulish:wght@300;600;700&family=Caveat:wght@400&family=Asap:ital,wght@1,700&family=Antonio:wght@400&family=Bebas+Neue&family=Alfa+Slab+One&family=Roboto+Condensed:ital,wght@1,300&display=swap">
<style>
  :root {
    --purple: #6f3f8f;
    --purple-band: #71408d;
    --teal: #1b8a95;
    --teal-top: #3fa39b;
    --green: #8fb44a;
    --yellow: #e6b925;
    --orange: #e39a52;
    --magenta: #b5206a;
    --grey-text: #7a7a7a;
    --label-grey: #8a8a8a;
    --rule-grey: #9a9a9a;
    --card-edge: #b8b8b8;
    --white: #ffffff;
  }
  * { margin: 0; padding: 0; box-sizing: border-box; }
  html, body { width: 1200px; height: 1200px; overflow: hidden; background: var(--white); }
  .sheet { position: relative; width: 1200px; height: 1200px; }

  .card {
    position: absolute;
    top: 450px;
    width: 480px;
    height: 300px;
    border: 1.5px solid var(--card-edge);
    background: var(--white);
    overflow: hidden;
  }
  .card svg { display: block; width: 100%; height: 100%; }
  .card--front { left: 100px; }
  .card--back { left: 620px; }

  .dimension-label,
  .side-label {
    position: absolute;
    font-family: "Roboto Condensed", sans-serif;
    font-style: italic;
    font-weight: 300;
    color: var(--label-grey);
    font-size: 32px;
    line-height: 1;
  }
  .dimension-label--width { left: 297px; top: 394px; }
  .dimension-label--height { left: 8px; top: 584px; }
  .side-label--front { left: 505px; top: 772px; }
  .side-label--back { left: 1030px; top: 772px; }

  .dimension-rule { position: absolute; background: var(--rule-grey); }
  .dimension-rule--width-left { left: 100px; top: 412px; width: 170px; height: 1px; }
  .dimension-rule--width-right { left: 410px; top: 412px; width: 170px; height: 1px; }
  .dimension-rule--height-top { left: 45px; top: 450px; width: 1px; height: 125px; }
  .dimension-rule--height-bottom { left: 45px; top: 630px; width: 1px; height: 120px; }

  .brand-name { font-family: "Mulish", sans-serif; font-weight: 600; fill: var(--grey-text); }
  .tagline { font-family: "Caveat", cursive; fill: var(--purple); }
  .coach-name-first { font-family: "Mulish", sans-serif; font-weight: 300; fill: var(--purple); }
  .coach-name-last { font-family: "Mulish", sans-serif; font-weight: 700; fill: var(--purple); }
  .coach-role { font-family: "Mulish", sans-serif; font-weight: 600; fill: var(--purple); letter-spacing: 1.6px; }
  .phone-line { font-family: "Mulish", sans-serif; font-weight: 600; fill: var(--purple); }
  .service-seminars { font-family: "Asap", sans-serif; font-style: italic; font-weight: 700; fill: var(--purple); }
  .service-coaching { font-family: "Antonio", sans-serif; font-weight: 400; fill: var(--teal); }
  .service-podcasts { font-family: "Bebas Neue", sans-serif; fill: var(--white); }
  .service-workshops { font-family: "Alfa Slab One", serif; fill: var(--magenta); }
  .contact-line { font-family: "Mulish", sans-serif; font-weight: 600; fill: var(--white); }
</style>
</head>
<body>
<main class="sheet">

  <span class="dimension-rule dimension-rule--width-left"></span>
  <span class="dimension-label dimension-label--width">80 mm</span>
  <span class="dimension-rule dimension-rule--width-right"></span>

  <span class="dimension-rule dimension-rule--height-top"></span>
  <span class="dimension-label dimension-label--height">50 mm</span>
  <span class="dimension-rule dimension-rule--height-bottom"></span>

  <!-- Front of card -->
  <section class="card card--front" aria-label="Business card front">
    <svg viewBox="0 0 480 300" xmlns="http://www.w3.org/2000/svg">
      <defs>
        <linearGradient id="front-green" x1="0" y1="0" x2="0" y2="1">
          <stop offset="0" stop-color="#8fb44a"/>
          <stop offset="1" stop-color="#7fae55"/>
        </linearGradient>
        <linearGradient id="front-sun" x1="0" y1="0" x2="1" y2="0.6">
          <stop offset="0" stop-color="#e39a52"/>
          <stop offset="0.55" stop-color="#e6b425"/>
          <stop offset="1" stop-color="#e6b925"/>
        </linearGradient>
      </defs>
      <path class="front-leaf" d="M0 0 H130 C118 45 122 95 118 115 C80 125 35 140 0 160 Z" fill="url(#front-green)"/>
      <path class="front-sun" d="M128 0 H310 C345 30 350 95 320 135 C290 172 240 188 195 180 C160 174 130 150 116 118 C122 80 118 40 128 0 Z" fill="url(#front-sun)"/>
      <circle class="brand-mark" cx="237" cy="99" r="68" fill="var(--purple)" stroke="var(--white)" stroke-width="5"/>
      <text class="brand-name" x="240" y="222" font-size="33" text-anchor="middle">Bright Core Living</text>
      <text class="tagline" x="235" y="258" font-size="28" text-anchor="middle">The journey home starts with you</text>
    </svg>
  </section>

  <!-- Back of card -->
  <section class="card card--back" aria-label="Business card back">
    <svg viewBox="0 0 480 300" xmlns="http://www.w3.org/2000/svg">
      <defs>
        <linearGradient id="back-green" x1="1" y1="0" x2="0.3" y2="1">
          <stop offset="0" stop-color="#3fa39b"/>
          <stop offset="0.55" stop-color="#7fb04f"/>
          <stop offset="1" stop-color="#8fb44a"/>
        </linearGradient>
        <linearGradient id="back-sun" x1="0" y1="0" x2="1" y2="0">
          <stop offset="0" stop-color="#e6b925"/>
          <stop offset="0.6" stop-color="#e6b425"/>
          <stop offset="1" stop-color="#e39a52"/>
        </linearGradient>
      </defs>

      <path class="back-wave" d="M408 0 H480 V236 H325 V128 C360 100 400 60 408 0 Z" fill="url(#back-green)"/>
      <path class="back-sun" d="M122 236 C126 165 165 108 225 98 C270 91 305 108 325 128 C340 160 345 200 352 236 Z" fill="url(#back-sun)"/>
      <path class="back-outline" d="M408 0 C400 60 360 100 325 128 C305 108 270 91 225 98" fill="none" stroke="var(--purple)" stroke-width="2"/>

      <text x="33" y="52" font-size="36"><tspan class="coach-name-first">Darren</tspan><tspan class="coach-name-last" dx="4">Whitlow</tspan></text>
      <line x1="34" y1="63" x2="298" y2="63" stroke="var(--purple)" stroke-width="2.5"/>
      <text class="coach-role" x="35" y="84" font-size="14.5">Health &amp; Wellbeing Life Coach</text>

      <text class="phone-line" x="110" y="160" font-size="26" text-anchor="end">0491</text>
      <text class="phone-line" x="110" y="188" font-size="26" text-anchor="end">372</text>
      <text class="phone-line" x="110" y="216" font-size="26" text-anchor="end">615</text>

      <text class="service-seminars" x="166" y="165" font-size="34">Seminars</text>
      <text class="service-coaching" x="156" y="226" font-size="60" textLength="172" lengthAdjust="spacingAndGlyphs">COACHING</text>
      <text class="service-podcasts" x="337" y="168" font-size="36" textLength="112" lengthAdjust="spacingAndGlyphs">PODCASTS</text>
      <text class="service-workshops" x="350" y="196" font-size="25">Work</text>
      <text class="service-workshops" x="350" y="222" font-size="25">shops</text>

      <rect class="contact-band" x="0" y="236" width="480" height="64" fill="var(--purple-band)"/>
      <g class="icon-mail" fill="none" stroke="var(--white)" stroke-width="1.6">
        <rect x="31" y="257" width="19" height="13" rx="1"/>
        <path d="M31 258 L40.5 265 L50 258"/>
      </g>
      <text class="contact-line" x="59" y="268" font-size="12.8">darren@brightcoreliving.example</text>
      <g class="icon-pointer" fill="var(--white)" stroke="#222" stroke-width="1">
        <path d="M287 254 v11 l-3 -2 l-2 2 l5 8 h9 l2 -8 v-5 h-3 v3 v-4 h-3 v4 v-5 h-3 v5 v-9 z"/>
      </g>
      <text class="contact-line" x="306" y="268" font-size="12.8">brightcoreliving.example</text>
    </svg>
  </section>

  <span class="side-label side-label--front">Front</span>
  <span class="side-label side-label--back">Back</span>

</main>
</body>
</html>
```